Tovin Brightway Website Design

About The Client:
Tovin Brightway is a sugar-free foods chain store providing services to Diabetics. They focus on the China domestic market. They describe themselves as being the 3rd space for Diabetics, the space between hospital and the home that help improve the quality of life for people wit Diabetes (see attached infographics).

They regularly hold education and advice events throughout the China. Tovin Brightway distribute a wide product range of food that is suitable for diabetic people. Tovin Brightway operate as a Franchise, providing business development services and Industry knowledge. They are actively seeking business partnerships at present.

The Brief:
Design a Home page and secondary information page(PSD only no code) that communicates our company services and company philosophy(3rd Space).
The final design should communicate 'Health, Social Responsibility and Professionalism'.
Colour scheme should orientate around Blue and White, see attached logo.

Websites we like:

http://lumo.vextaran.com/home/

https://www.pondrelix.com/

http://gate.zt.com/

Hello all, the client has advised us that he want to display the professional advice service available for diabetic people more so than a food distributor. The client is also hoping to use his website as a marketing platform to attract affiliates and build partnerships as part of Tovin Brightway's business expansion strategy.

So can you make the page more corporate, reliable and professional. Use images of experts/doctors interacting with patients and also training/knowledge transfer images.

Thanks

Hello all, could you include stock images of both Chinese and Caucasians

Yeaahhh, Infographics and photos have been uploaded. Feel free to use them in your designs and also as references.

Target Market(s)

The target market is Chinese B2B in the Diabetics industry and Entrepreneurs looking to cooperate with Tovin Brightway.

Industry/Entity Type

Education

Requirements
Must have
• menu navigation with 7-8 sections,
a full screen background image,
Social Media icons,
Logo in top left,
Site search.
Nice to have
• The website must be clear and easy to use, less complicated.

See attached files of some Tovin Brightway infographics. Feel free to include elements of these into the design.
Should not have
• Should not use stock images of people from any other country, the client wants stock images of Chinese people only. Avoid photos showing obesity.

```html
<!DOCTYPE html>
<html lang="en">
<head>
<meta charset="utf-8">
<title>Tovin Brightway — Home</title>
<link rel="stylesheet" href="https://fonts.googleapis.com/css2?family=Roboto+Condensed:wght@300;400;700&display=swap">
<style>
:root{
  --blue:#1479b8;
  --blue-bright:#2aa6e8;
  --blue-deep:#0c6aa9;
  --red:#e0252f;
  --red-deep:#b8161e;
  --ink:#444;
  --muted:#666;
  --page:#f4f3f3;
  --white:#fff;
  --line:#d6d6d6;
}
*{box-sizing:border-box;margin:0;padding:0}
html,body{width:1188px;height:1200px;overflow:hidden}
body{font-family:"Roboto Condensed",Arial,sans-serif;background:var(--page);color:var(--ink);position:relative}
.site-header{position:absolute;left:0;top:0;width:1188px;height:103px;background:var(--white)}
.brand{position:absolute;left:179px;top:28px;display:flex;align-items:center;gap:10px;color:var(--blue-bright);font-size:24px;font-weight:400}
.brand-mark{width:30px;height:30px;border-radius:50%;background:var(--blue-bright)}
.social{position:absolute;left:792px;top:26px;display:flex;gap:10px}
.social span{width:16px;height:16px;border-radius:3px;background:var(--blue-bright)}
.search{position:absolute;left:855px;top:16px;width:180px;height:33px;border:1px solid #d4d4d4;background:#fff;font-size:14px;color:#777;padding:8px 9px}
.search svg{position:absolute;right:8px;top:7px}
.main-nav{position:absolute;right:152px;top:66px;display:flex}
.main-nav a{font-size:16px;color:#555;text-decoration:none;padding:2px 12px 17px;position:relative}
.main-nav a.active{color:var(--blue-bright)}
.main-nav a.active::after{content:"";position:absolute;left:0;right:0;bottom:0;height:3px;background:var(--blue-bright)}
.hero{position:absolute;left:0;top:103px;width:1188px;height:441px;background:linear-gradient(90deg,#5c6a76,#4b5864 50%,#3d4853);overflow:hidden}
.hero-grid{position:absolute;inset:0;background-image:linear-gradient(rgba(255,255,255,.05) 1px,transparent 1px),linear-gradient(90deg,rgba(255,255,255,.05) 1px,transparent 1px);background-size:26px 26px}
.hero-heart{position:absolute;left:523px;top:30px}
.hero-tagline{position:absolute;left:183px;top:302px;color:#fff;font-size:27px;font-weight:300;line-height:32px}
.hero-tagline strong{color:var(--blue-bright);font-weight:700}
.slider-dots{position:absolute;left:530px;top:528px;width:108px;height:32px;border-radius:16px;background:linear-gradient(#fff,#e8e8e8);box-shadow:0 3px 6px rgba(0,0,0,.2);display:flex;gap:8px;justify-content:center;align-items:center}
.slider-dots i{width:14px;height:14px;border-radius:50%;border:1px solid #bbb;background:#f4f4f4}
.slider-dots i.on{background:#ccc}
.feature{position:absolute;top:591px;width:287px;height:244px;border:1px solid #d3d3d3;background:#f1f1f1;text-align:center}
.feature h2{font-size:16px;color:var(--blue);font-weight:700;margin-top:14px}
.feature-photo{margin:9px auto 0;width:252px;height:101px;border:1px solid #ccc;background:#fff;padding:5px}
.feature-photo div{width:100%;height:100%}
.feature p{font-size:12.5px;line-height:15px;color:var(--muted);margin:7px 14px 0}
.btn{display:inline-block;color:#fff;font-weight:700;text-align:center;text-decoration:none;border-radius:2px;background:linear-gradient(#3cb4ee,var(--blue-deep));box-shadow:0 1px 2px rgba(0,0,0,.25)}
.feature .btn{width:114px;height:29px;line-height:29px;font-size:12.5px;margin-top:9px}
.section-title{font-size:16px;color:#555;font-weight:300;padding-bottom:8px;border-bottom:1px dashed #aaa}
.section-title b{color:var(--blue);font-weight:700}
.welcome{position:absolute;left:147px;top:864px;width:587px}
.welcome p{font-size:12.5px;line-height:14.5px;color:var(--muted);margin-top:16px}
.cta-row{display:flex;gap:8px;margin-top:23px}
.cta-row .btn{width:189px;height:45px;line-height:45px;font-size:15px;border-radius:3px}
.cta-row .btn.red{background:linear-gradient(#f06068,var(--red) 50%,var(--red-deep))}
.query{position:absolute;left:747px;top:864px;width:290px}
.field{display:block;width:290px;background:#fff;border:1px solid #d0d0d0;font-size:12.5px;color:#555;padding:8px 6px}
.field.email{margin-top:13px;height:30px;padding-top:7px}
.field.message{margin-top:8px;height:90px}
.query .btn{position:absolute;right:-1px;top:179px;width:114px;height:29px;line-height:29px;font-size:12.5px}
.site-footer{position:absolute;left:0;top:1104px;width:1188px;height:96px;background:#fff;border-top:1px solid #ddd;text-align:center;font-size:11.5px;color:#666;line-height:17px;padding-top:28px}
</style>
</head>
<body>
<header class="site-header">
  <div class="brand"><span class="brand-mark"></span>Tovin Brightway</div>
  <div class="social"><span></span><span></span></div>
  <div class="search">Search
    <svg width="18" height="18" viewBox="0 0 18 18"><circle cx="7" cy="7" r="5.5" fill="none" stroke="#2b7fc0" stroke-width="1.6"/><line x1="11" y1="11" x2="16.5" y2="16.5" stroke="#2b7fc0" stroke-width="2"/></svg>
  </div>
  <nav class="main-nav">
    <a class="active" href="#">Home</a><a href="#">About Us</a><a href="#">Services</a><a href="#">Food Store</a><a href="#">Our Philosophy</a><a href="#">Events</a><a href="#">Contact Us</a>
  </nav>
</header>

<section class="hero" role="img" aria-label="Interior of the diabetes care store with product shelves">
  <div class="hero-grid"></div>
  <svg class="hero-heart" width="476" height="400" viewBox="0 0 476 400" role="img" aria-label="Heart-shaped photo of an advisor talking with customers">
    <defs><linearGradient id="heartFill" x1="0" y1="0" x2="0" y2="1"><stop offset="0" stop-color="#e8eef2"/><stop offset=".45" stop-color="#c9b9a4"/><stop offset="1" stop-color="#6e6a70"/></linearGradient></defs>
    <path d="M238 398 L28 168 C-12 115 4 18 92 4 C160 -6 214 28 238 86 C262 28 316 -6 384 4 C472 18 488 115 448 168 Z" fill="url(#heartFill)"/>
  </svg>
  <p class="hero-tagline">We just not only sale food but<br>also made our <strong>Social Responsibilities</strong>.</p>
</section>
<div class="slider-dots"><i class="on"></i><i></i><i></i><i></i></div>

<article class="feature" style="left:146px">
  <h2>Our Philosophy</h2>
  <div class="feature-photo"><div role="img" aria-label="Woman stretching in a bright room" style="background:linear-gradient(90deg,#cfcfcf,#ececec,#d4d4d4)"></div></div>
  <p>Lorem ipsum dolor sit amet, consectetur adipisicing elit, sed do eiusmod tempor incididunt ut labore et dolore magna aliqua.</p>
  <a class="btn" href="#">Know More</a>
</article>
<article class="feature" style="left:447px">
  <h2>Our Services</h2>
  <div class="feature-photo"><div role="img" aria-label="Smiling staff member in a kitchen" style="background:linear-gradient(90deg,#b9bfc6,#e6e1dc,#c9c6c2)"></div></div>
  <p>Lorem ipsum dolor sit amet, consectetur adipisicing elit, sed do eiusmod tempor incididunt ut labore et dolore magna aliqua.</p>
  <a class="btn" href="#">Know More</a>
</article>
<article class="feature" style="left:747px">
  <h2>Our Events</h2>
  <div class="feature-photo"><div role="img" aria-label="Customers at a store event among colourful shelves" style="background:linear-gradient(90deg,#c9a26b,#9fb4c7,#c7664f)"></div></div>
  <p>Lorem ipsum dolor sit amet, consectetur adipisicing elit, sed do eiusmod tempor incididunt ut labore et dolore magna aliqua.</p>
  <a class="btn" href="#">Know More</a>
</article>

<section class="welcome">
  <h3 class="section-title"><b>Welcome</b> to our site</h3>
  <p>Lorem ipsum dolor sit amet, consectetur adipisicing elit, sed do eiusmod tempor incididunt ut labore et dolore magna aliqua. Lorem ipsum dolor sit amet, consectetur adipisicing elit, sed do eiusmod tempor incididunt ut labore et dolore magna aliqua. Lorem ipsum dolor sit amet, consectetur adipisicing elit, sed do eiusmod tempor incididunt ut labore et dolore magna aliqua.</p>
  <div class="cta-row">
    <a class="btn" href="#">OUR TRAINING</a>
    <a class="btn red" href="#">PERTNERSHIP</a>
    <a class="btn" href="#">FOR DIABETICS</a>
  </div>
</section>

<section class="query">
  <h3 class="section-title"><b>Query Us</b> to help you</h3>
  <div class="field email">Email</div>
  <div class="field message">Query</div>
  <a class="btn" href="#">Submit</a>
</section>

<footer class="site-footer">Copyright@2013. All rights are reserved.<br>Terms &amp; Privacy Policy</footer>
</body>
</html>
```